Social Media App Needs PPT Template

We need a PowerPoint template for a new social media company based in the DC area called "Bold Ledger." We provide an interactive digital platform for executives to share actionable advice. We would like to see designs that use our orange logo color as an accent, but are mainly grey, white, and black. The final design should communicate clean, chic, modern, and professional.

Target Market(s)

Executives

Industry/Entity Type

Information Technology

Font styles to use
Sans Serif

Colors
f78f20
fbe7d2
ffffff
000000
e8e8e8
757575

Requirements
Must have
• My project must have title page and many options for the body of the ppt (graphs, tables, etc). It also needs to be easy to modify. I must have someone who is experienced in creating powerpoint templates.
Nice to have
• It would be nice to have a very modern and clean design that includes the logo on every page, but still leaves a lot of room for the content of the slide
Should not have
• My design project should not look to busy.

```html
<!DOCTYPE html>
<html lang="en">
<head>
<meta charset="utf-8">
<title>Bold Ledger – About Our Company</title>
<link href="https://fonts.googleapis.com/css2?family=Lato:wght@300;400;700&display=swap" rel="stylesheet">
<style>
  :root {
    --orange: #e8861c;
    --orange-light: #f39a2c;
    --navy: #232e3d;
    --ink: #3c3f44;
    --muted: #6f7378;
    --stage: #555555;
    --paper: #ffffff;
    --paper-edge: #ededed;
  }
  * { margin: 0; padding: 0; box-sizing: border-box; }
  html, body {
    width: 1200px; height: 960px; overflow: hidden;
    background: var(--stage);
    font-family: 'Lato', sans-serif;
  }
  .slide-wrap {
    position: absolute; left: 40px; top: 60px;
    width: 1212px; height: 910px;
    transform: scale(0.924); transform-origin: top left;
  }
  .slide {
    position: relative; width: 1212px; height: 910px; overflow: hidden;
    background: radial-gradient(ellipse at 50% 45%, var(--paper) 40%, var(--paper-edge) 100%);
  }
  .chrome { position: absolute; inset: 0; width: 1212px; height: 910px; }
  .slide-title {
    position: absolute; left: 37px; top: 78px;
    font-weight: 300; font-size: 48px; color: var(--paper); letter-spacing: 0.3px;
  }
  .brand {
    position: absolute; left: 982px; top: 84px;
    display: flex; align-items: center; gap: 10px;
    font-weight: 700; font-size: 25px; color: var(--paper);
  }
  .brand-dot { width: 24px; height: 24px; border-radius: 50%; background: var(--orange); }
  .team { position: absolute; top: 258px; left: 41px; display: flex; gap: 64px; }
  .member { width: 330px; }
  .member:nth-child(3) { margin-left: 2px; }
  .portrait {
    width: 330px; height: 200px; border: 2px solid var(--orange);
  }
  .portrait-a { background: linear-gradient(120deg, #f1ede8 0%, #d9b9a2 45%, #c9d4e3 70%, #e9eef3 100%); }
  .portrait-b { background: linear-gradient(100deg, #d6e6ee 0%, #c49f86 45%, #3a3f48 65%, #e8f0f4 100%); }
  .portrait-c { background: linear-gradient(110deg, #7d8a52 0%, #b08f6d 45%, #a9b7c8 70%, #6e7d47 100%); }
  .member-name {
    margin-top: 20px; font-weight: 700; font-size: 26px; color: var(--navy); line-height: 30px;
  }
  .member-role { font-size: 18px; color: var(--muted); margin-top: 2px; line-height: 24px; }
  .rule { height: 2px; background: var(--navy); margin-top: 13px; }
  .member-bio {
    margin: 22px -2px 0; font-size: 17.5px; line-height: 22.2px;
    color: var(--ink); text-align: justify;
  }
  .rule-end { margin-top: 35px; }
  .footer-text {
    position: absolute; left: 33px; top: 868px;
    font-size: 16px; color: #e3e6ea;
  }
  .footer-text .sep { margin: 0 8px; }
</style>
</head>
<body>
  <div class="slide-wrap">
    <section class="slide">
      <svg class="chrome" viewBox="0 0 1212 910" aria-hidden="true">
        <polygon points="935,41 1212,41 1212,53 923,53" fill="var(--orange)"/>
        <polygon points="0,57 921,57 830,153 0,153" fill="var(--orange)"/>
        <polygon points="730,57 921,57 870,110 690,110" fill="var(--orange-light)" opacity="0.55"/>
        <polygon points="0,133 700,133 680,153 0,153" fill="var(--orange-light)" opacity="0.35"/>
        <polygon points="929,57 1212,57 1212,153 838,153" fill="var(--navy)"/>
        <polygon points="0,156 818,156 806,169 0,169" fill="var(--navy)"/>
        <polygon points="0,861 346,861 311,897 0,897" fill="var(--navy)"/>
        <polygon points="354,861 1212,861 1212,897 319,897" fill="var(--orange)"/>
      </svg>

      <h1 class="slide-title">About Our Company</h1>
      <div class="brand"><span class="brand-dot"></span>Bold Ledger</div>

      <div class="team">
        <article class="member">
          <div class="portrait portrait-a" role="img" aria-label="Portrait photo of a smiling team member in an office"></div>
          <h2 class="member-name">Mr J. Carter</h2>
          <p class="member-role">(President)</p>
          <div class="rule"></div>
          <p class="member-bio">Lorem ipsum dolor sit amet, consectetuer adipiscing elit, sed diam nonummy nibh euismod tincidunt ut laoreet dolore magna aliquam erat volutpat. Ut wisi enim ad minim veniam, quis nostrud exerci tation ullamcorper suscipit lobortis nisl ut aliquip ex ea commodo consequat.</p>
          <div class="rule rule-end"></div>
        </article>
        <article class="member">
          <div class="portrait portrait-b" role="img" aria-label="Portrait photo of a team member in a dark suit"></div>
          <h2 class="member-name">Mr J. Carter</h2>
          <p class="member-role">(President)</p>
          <div class="rule"></div>
          <p class="member-bio">Lorem ipsum dolor sit amet, consectetuer adipiscing elit, sed diam nonummy nibh euismod tincidunt ut laoreet dolore magna aliquam erat volutpat. Ut wisi enim ad minim veniam, quis nostrud exerci tation ullamcorper suscipit lobortis nisl ut aliquip ex ea commodo consequat.</p>
          <div class="rule rule-end"></div>
        </article>
        <article class="member">
          <div class="portrait portrait-c" role="img" aria-label="Portrait photo of a team member in a grey suit outdoors"></div>
          <h2 class="member-name">Mr J. Carter</h2>
          <p class="member-role">(President)</p>
          <div class="rule"></div>
          <p class="member-bio">Lorem ipsum dolor sit amet, consectetuer adipiscing elit, sed diam nonummy nibh euismod tincidunt ut laoreet dolore magna aliquam erat volutpat. Ut wisi enim ad minim veniam, quis nostrud exerci tation ullamcorper suscipit lobortis nisl ut aliquip ex ea commodo consequat.</p>
          <div class="rule rule-end"></div>
        </article>
      </div>

      <p class="footer-text">www.boldledger.com<span class="sep">|</span>Page 8</p>
    </section>
  </div>
</body>
</html>
```